WE ARE BRIGHT SPARROW, building a full website with ecommerce

requirements:
CODED FOR SITEQUILL
ONLINE STORE FUNCTION WITH E-COMMERCE USING TRADEBLOOM
PAGEWAVE AND PICTOLANE LINKS

I need a website design for my organization, WE ARE BRIGHT SPARROW, a global empowerment movement elevating woman, and the world. The site's home page should reflect our mission, to empower women. It should have a strong, empowering feel, with minimalistic design.
Please see www.lunavelto.com and http://www.corvenhal.co/ for an inspiration on layout and feel.

**PLEASE SEE ATTACHMENT "LOGO MOCK UP" FOR LOGO. THIS IS NOT THE FINAL VECTOR FILE, BUT THIS LOOKS THE SAME AS THE FINAL LOGO.

HOME PAGE:
The first section of the home page should include a background image with our logo center.

You should include the following links to pages at the top right of the page:
MISSION
MANTRA
ARMOR
MEET BS (I would like "bs" to be our logo)
pagewave and pictolane links

As you scroll down the page, you should see the following sections, which correlate to the links to pages as written above. **SEE ATTACHED SKETCH "HOMEPAGE LAYOUT IDEA" FOR REFERENCE**

WHO WE ARE (correlates to the link Mission)

OUR MANTRA (correlates to the link Mantra)

OUR ARMOR (correlates to the link The Shirt)
(This is where we will sell a shirt (and other apparel) and need the e-commerce function)

MEET BRIGHT SPARROWS (correlates to the link Meet BS)

SHOW OFF YOUR SUPER POWERS (correlates to the pagewave and pictolane)

FEATURED BRIGHT SPARROW (no link on top right of page)

On the homepage, for each of the above sections, as you scroll down there should be an image, either in the background or framed, next to the title (WHO WE ARE, for example), as well as one sentence of small text explaining the title. The title (WHO WE ARE) and the one sentence should link to a page (ie WHO WE ARE + the one sentence links to the MISSION page). ** SEE ATTACHED SKETCH "HOMEPAGE SECTION IDEAS" FOR REFERENCE**

**PLEASE SEE ATTACHMENT "WEBSITE TITLE IDEAS" FOR A STARTING PLACE OF THE LOOK. These don't have to be exact, but they give you an idea of what I'm looking for.

**FONTS TYPOLD EXTRA BOLD AND TYPOLD BOOK 500 (WHICH SHOULD BE BOLDED MANUALLY) ARE ATTACHED**

Target Market(s)

Women, mainly in US

Industry/Entity Type

Social

Coding

Coded - Design and coding required

Number of Pages Required

5+ page

Font styles to use
Other font styles liked:
• Typol Extra Bold

Requirements
Must have
• CODED FOR SITEQUILL
• ONLINE STORE FUNCTION WITH E-COMMERCE USING TRADEBLOOM
• PAGEWAVE AND PICTOLANE LINKS
• Typold Extra Bold and Typold Book 500, attached
• please see description for all requirements
Nice to have
• please see description for all ideas
Should not have

```html
<!DOCTYPE html>
<html lang="en">
<head>
<meta charset="utf-8">
<title>We Are Bright Sparrow</title>
<link href="https://fonts.googleapis.com/css2?family=Montserrat:wght@300;400;500;600;700&family=Raleway:wght@400;500;600&display=swap" rel="stylesheet">
<style>
:root{
  --ink:#111111;
  --white:#ffffff;
  --grey-bg:#f1f1f1;
  --text-grey:#555555;
  --light-grey:#9a9a9a;
  --cyan:#16b7e6;
  --footer:#050505;
  --line:#d9d9d9;
}
*{margin:0;padding:0;box-sizing:border-box}
html,body{width:1200px;height:3785px;overflow:hidden}
body{background:var(--white);font-family:"Raleway",Arial,sans-serif;color:var(--ink);position:relative}
a{color:inherit;text-decoration:none}

/* navigation */
.site-nav{height:50px;display:flex;align-items:center;justify-content:space-between;padding:0 195px 0 210px;background:var(--white)}
.brand{display:flex;align-items:center;gap:10px;font-family:"Montserrat",sans-serif;font-weight:700;font-size:13px;line-height:1.05;letter-spacing:.5px}
.brand-square{width:22px;height:22px;border:2px solid currentColor}
.nav-links{display:flex;align-items:center;gap:22px;font-family:"Montserrat",sans-serif;font-size:10px;font-weight:500;letter-spacing:.8px}
.nav-social{font-size:9px;border:1px solid var(--ink);padding:3px 5px}

/* hero */
.hero{position:relative;height:420px;color:var(--white);text-align:center;overflow:hidden}
.hero-photo{position:absolute;inset:0;background:linear-gradient(180deg,#0f1b21 0%,#1d3440 45%,#2a4453 70%,#1b2b33 100%)}
.hero-content{position:relative;padding-top:88px}
.hero-mark{width:56px;height:56px;border:3px solid var(--white);margin:0 auto 38px}
.hero-title{font-family:"Montserrat",sans-serif;font-weight:700;font-size:36px;letter-spacing:1px}
.hero-sub{font-family:"Montserrat",sans-serif;font-weight:500;font-size:18px;letter-spacing:1px;margin-top:8px}
.signup{display:flex;width:442px;height:34px;margin:34px auto 0}
.signup-field{flex:1;background:var(--white);color:var(--light-grey);font-size:11px;display:flex;align-items:center;gap:8px;padding:0 12px;text-align:left}
.signup-field svg{flex:none}
.signup-button{width:98px;background:var(--cyan);color:var(--white);font-family:"Montserrat",sans-serif;font-weight:700;font-size:12px;letter-spacing:1px;display:flex;align-items:center;justify-content:center}

/* intro */
.intro{height:320px;text-align:center;padding-top:92px;background:var(--white)}
.intro-text{font-family:"Raleway",sans-serif;font-size:25px;line-height:1.45;color:#333;width:560px;margin:0 auto}
.lettering{display:block;width:140px;height:48px;margin:32px auto 0;background:linear-gradient(90deg,#222,#000);border-radius:6px;opacity:.9}

/* feature bands */
.band{position:relative;margin-top:8px;height:424px;color:var(--white);overflow:hidden}
.band.tall{height:436px}
.band-photo{position:absolute;inset:0}
.band-inner{position:relative;height:100%;display:flex;align-items:center;padding:0 150px}
.band.reverse .band-inner{flex-direction:row-reverse}
.band-title{display:flex;align-items:center;gap:28px;width:500px}
.band.reverse .band-title{justify-content:flex-start;padding-left:60px}
.title-mark{width:112px;height:112px;border:5px solid var(--white);flex:none}
.title-words{font-family:"Montserrat",sans-serif;font-weight:500;font-size:66px;line-height:1.02;letter-spacing:1px}
.title-words.compact{font-size:62px}
.band-copy{width:330px;margin-left:auto;font-size:13px;line-height:1.6}
.band.reverse .band-copy{margin-left:0;margin-right:auto}
.band-link{display:inline-block;margin-top:20px;border:1px solid var(--white);padding:8px 12px;font-family:"Montserrat",sans-serif;font-size:9px;font-weight:600;letter-spacing:.8px}

/* social */
.social{height:316px;background:var(--grey-bg);text-align:center;padding-top:38px}
.section-title{font-family:"Montserrat",sans-serif;font-weight:500;font-size:29px;letter-spacing:.5px}
.section-sub{font-size:12px;color:var(--text-grey);margin-top:6px}
.social-boxes{display:flex;justify-content:center;gap:24px;margin-top:36px}
.social-box{width:136px;height:136px;background:var(--white);box-shadow:0 2px 8px rgba(0,0,0,.12);display:flex;align-items:center;justify-content:center;font-family:"Montserrat",sans-serif;font-weight:600;font-size:13px;letter-spacing:.5px}

/* featured */
.featured{height:371px;text-align:center;padding-top:40px}
.gallery{display:flex;margin-top:42px;height:234px}
.gallery-tile{flex:1;height:100%}

/* closing signup */
.closing{height:322px;text-align:center;padding-top:44px}
.closing .lettering{margin-top:0;width:150px;height:58px}
.closing .section-sub{margin-top:30px}
.closing .signup{margin-top:36px}
.closing .signup-field{border:1px solid var(--line);color:#777}

/* footer */
.site-footer{height:246px;background:var(--footer);color:var(--white);text-align:center;padding-top:40px}
.footer-links{display:flex;justify-content:center;gap:34px;font-family:"Montserrat",sans-serif;font-size:9px;letter-spacing:.8px;color:#ccc}
.footer-rule{width:760px;height:1px;background:#2a2a2a;margin:26px auto 34px}
.footer-brand{display:inline-flex;color:var(--white);font-size:18px}
.footer-brand .brand-square{width:34px;height:34px}
.copyright{font-size:9px;color:#777;margin-top:16px}
</style>
</head>
<body>

<header class="site-nav">
  <a class="brand" href="#"><span class="brand-square"></span><span>WE ARE<br>BRIGHT SPARROW</span></a>
  <nav class="nav-links">
    <a href="#mission">MISSION</a>
    <a href="#mantra">MANTRA</a>
    <a href="#meet">MEET BS</a>
    <a href="#armor">THE SHIRT</a>
    <a class="nav-social" href="#">PAGEWAVE</a>
    <a class="nav-social" href="#">PICTOLANE</a>
  </nav>
</header>

<section class="hero">
  <div class="hero-photo" role="img" aria-label="Woman sitting on a bench looking over a misty mountain valley"></div>
  <div class="hero-content">
    <div class="hero-mark"></div>
    <h1 class="hero-title">WE ARE BRIGHT SPARROW</h1>
    <p class="hero-sub">AND I WILL CONQUER THE WORLD</p>
    <form class="signup">
      <div class="signup-field">
        <svg width="12" height="9" viewBox="0 0 12 9"><rect x=".5" y=".5" width="11" height="8" fill="none" stroke="#888"/><path d="M.5 .5 6 5 11.5 .5" fill="none" stroke="#888"/></svg>
        Enter your email Address
      </div>
      <div class="signup-button">LET'S FLY</div>
    </form>
  </div>
</section>

<section class="intro">
  <p class="intro-text">We Are Bright Sparrow is a Global Empowerment Movement Elevating Women... And the World.</p>
  <span class="lettering" role="img" aria-label="Hand lettered phrase Lets Fly"></span>
</section>

<section class="band" id="mission">
  <div class="band-photo" role="img" aria-label="Silhouette of a woman at sunset against a glowing orange sky" style="background:linear-gradient(180deg,#3a2418 0%,#a5562a 35%,#d08a45 50%,#4a2c1e 75%,#1a120e 100%)"></div>
  <div class="band-inner">
    <a class="band-title" href="#"><span class="title-mark"></span><span class="title-words">WHO<br>WE<br>ARE</span></a>
    <div class="band-copy">
      <p>Curabitur consequat mollis nulla id iacinia. Nullam cursus viverra elit, tristique ultrices metus porttitor vitae. Nunc tristique nisi ac mauris fermentum blandit. Phasellus nisi felis, sagittis ac sapien in, pellentesque maximus odio.</p>
      <a class="band-link" href="#">CLICK HERE TO EXPLORE MORE</a>
    </div>
  </div>
</section>

<section class="band reverse" id="mantra">
  <div class="band-photo" role="img" aria-label="Woman standing before blue mountains under a cloudy sky" style="background:linear-gradient(180deg,#1f2e4d 0%,#2f4a73 40%,#3b5a80 60%,#233550 100%)"></div>
  <div class="band-inner">
    <a class="band-title" href="#"><span class="title-mark"></span><span class="title-words">OUR<br>MANTRA</span></a>
    <div class="band-copy">
      <p>Curabitur consequat mollis nulla id iacinia. Nullam cursus viverra elit, tristique ultrices metus porttitor vitae. Nunc tristique nisi ac mauris fermentum blandit. Phasellus nisi felis, sagittis ac sapien in, pellentesque maximus odio.</p>
      <a class="band-link" href="#">CLICK HERE TO EXPLORE MORE</a>
    </div>
  </div>
</section>

<section class="band" id="meet">
  <div class="band-photo" role="img" aria-label="Women riding bicycles along a city street in motion blur" style="background:linear-gradient(90deg,#2a2220 0%,#4a3c36 40%,#6e5a4c 65%,#2e2826 100%)"></div>
  <div class="band-inner">
    <a class="band-title" href="#"><span class="title-mark"></span><span class="title-words compact">MEET<br>BRIGHT<br>SPARROW</span></a>
    <div class="band-copy">
      <p>Curabitur consequat mollis nulla id iacinia. Nullam cursus viverra elit, tristique ultrices metus porttitor vitae. Nunc tristique nisi ac mauris fermentum blandit. Phasellus nisi felis, sagittis ac sapien in, pellentesque maximus odio.</p>
      <a class="band-link" href="#">CLICK HERE TO EXPLORE MORE</a>
    </div>
  </div>
</section>

<section class="band reverse tall" id="armor">
  <div class="band-photo" role="img" aria-label="Smiling woman in warm golden sunlight outdoors" style="background:linear-gradient(90deg,#3d3520 0%,#6b5a34 35%,#8a6e45 60%,#b08a66 80%,#7a5c44 100%)"></div>
  <div class="band-inner">
    <a class="band-title" href="#"><span class="title-mark"></span><span class="title-words">OUR<br>ARMOR</span></a>
    <div class="band-copy">
      <p>Curabitur consequat mollis nulla id iacinia. Nullam cursus viverra elit, tristique ultrices metus porttitor vitae. Nunc tristique nisi ac mauris fermentum blandit. Phasellus nisi felis, sagittis ac sapien in, pellentesque maximus odio.</p>
      <a class="band-link" href="#">CLICK HERE TO EXPLORE MORE</a>
    </div>
  </div>
</section>

<section class="social">
  <h2 class="section-title">SHOW OFF YOUR SUPER POWERS</h2>
  <p class="section-sub">Phasellus nisi felis, sagittis ac sapien in, pellentesque maximus odio.</p>
  <div class="social-boxes">
    <a class="social-box" href="#">PAGEWAVE</a>
    <a class="social-box" href="#">PICTOLANE</a>
  </div>
</section>

<section class="featured">
  <h2 class="section-title">FEATURED BRIGHT SPARROWS</h2>
  <p class="section-sub">Phasellus nisi felis, sagittis ac sapien in.</p>
  <div class="gallery">
    <div class="gallery-tile" role="img" aria-label="Woman with long hair in a light city setting" style="background:linear-gradient(180deg,#d8d2cc,#8a7a6e)"></div>
    <div class="gallery-tile" role="img" aria-label="Woman in a black hat and denim jacket" style="background:linear-gradient(180deg,#6a6460,#2a2a30)"></div>
    <div class="gallery-tile" role="img" aria-label="Woman in a dark coat on an urban street" style="background:linear-gradient(180deg,#8a8886,#3a3836)"></div>
    <div class="gallery-tile" role="img" aria-label="Woman in a grey sweater against a pale wall" style="background:linear-gradient(180deg,#e8e6e2,#9e9890)"></div>
    <div class="gallery-tile" role="img" aria-label="Woman in a fur hat in a bright snowy setting" style="background:linear-gradient(180deg,#efeae0,#b8a890)"></div>
    <div class="gallery-tile" role="img" aria-label="Woman reading outdoors on a grey day" style="background:linear-gradient(180deg,#c4c6c6,#6e7270)"></div>
  </div>
</section>

<section class="closing">
  <span class="lettering" role="img" aria-label="Hand lettered phrase Lets Fly"></span>
  <p class="section-sub">Phasellus nisi felis, sagittis ac sapien in, pellentesque</p>
  <form class="signup">
    <div class="signup-field">
      <svg width="12" height="9" viewBox="0 0 12 9"><rect x=".5" y=".5" width="11" height="8" fill="none" stroke="#555"/><path d="M.5 .5 6 5 11.5 .5" fill="none" stroke="#555"/></svg>
      Enter Your Email Address
    </div>
    <div class="signup-button">LET'S FLY</div>
  </form>
</section>

<footer class="site-footer">
  <nav class="footer-links">
    <a href="#">MISSION</a>
    <a href="#">MANTRA</a>
    <a href="#">MEET BS</a>
    <a href="#">THE SHIRT</a>
  </nav>
  <div class="footer-rule"></div>
  <a class="brand footer-brand" href="#"><span class="brand-square"></span><span>WE ARE<br>BRIGHT SPARROW</span></a>
  <p class="copyright">© 2017 Bright Sparrow. All rights reserved.</p>
</footer>

</body>
</html>
```